NEW Modern Sleek Business Card for VR Language Startup

Our startup is using VR to lead the next wave of world language education. We need a two-sided business card that introduces the larger organization (Brightloom Language Inc) and our contact info on one side and shows the product, Glimwoorld, on the other side.

Side 1 (contact info)= Brightloom Logo and Contact info (name, title, phone, email)

Side 2 (product)= Glimworld logo, text, and website
Text= Culturally Immersive Language Learning Games
Website= www.glimworld-play.com

Target Market(s)

Education, Technology

Contact Information for Business Card

Contact info will be updated upon approval of the design. For now, put this as a placeholder.

Perry Dunmore
Founder & CEO
pdunmore@quillpost-mail.net
(555)-014-2286

Font styles to use
Other font styles liked:
• Gibson and Century Gothic are the brand fonts

Requirements
Nice to have
• I would love to see cohesion between the design and colors of the two logos. I have attached a few business card designs that I like, so you can get a feel for my preferred style.

```html
<!DOCTYPE html>
<html lang="en">
<head>
<meta charset="utf-8">
<title>Glimworld &amp; Brightloom Business Card</title>
<link href="https://fonts.googleapis.com/css2?family=Montserrat:wght@400;700&family=Questrial&display=swap" rel="stylesheet">
<style>
  :root {
    --backdrop: #e4e4e6;
    --card-dark: #0c0c0d;
    --card-mid: #1d1d1f;
    --card-light: #2a2a2c;
    --ink-white: #f4f4f4;
    --ink-grey: #8a8a8c;
    --brand-blue: #4d86f4;
    --brand-violet: #6a5cf0;
    --band-orange: #fb7438;
    --band-red: #f2344f;
    --band-purple: #914fc8;
    --band-cyan: #1de3ea;
  }
  * { box-sizing: border-box; margin: 0; padding: 0; }
  html, body { width: 1200px; height: 1200px; overflow: hidden; }
  body {
    background: var(--backdrop);
    position: relative;
    font-family: "Questrial", "Century Gothic", sans-serif;
  }
  .card {
    position: absolute;
    left: 150px;
    width: 900px;
    height: 514px;
    border-radius: 28px;
    overflow: hidden;
    background: linear-gradient(115deg, var(--card-dark) 0%, var(--card-mid) 55%, var(--card-light) 100%);
    box-shadow: 0 18px 40px rgba(0,0,0,0.25);
  }
  .card--product { top: 60px; }
  .card--contact { top: 626px; }

  /* Product side */
  .product-mark {
    position: absolute;
    left: 0; right: 0; top: 170px;
    display: flex; align-items: center; justify-content: center; gap: 18px;
  }
  .product-mark__dot {
    width: 34px; height: 34px; border-radius: 50%;
    background: var(--brand-violet);
  }
  .product-mark__name {
    font-family: "Questrial", "Century Gothic", sans-serif;
    font-size: 76px;
    color: var(--brand-blue);
    letter-spacing: 1px;
  }
  .product-tagline {
    position: absolute; left: 0; right: 0; top: 292px;
    text-align: center;
    font-size: 25px;
    letter-spacing: 1px;
    color: var(--brand-blue);
  }
  .product-url {
    position: absolute; left: 0; right: 0; top: 384px;
    text-align: center;
    font-family: "Montserrat", sans-serif;
    font-weight: 700;
    font-size: 22px;
    letter-spacing: 1px;
    color: var(--brand-blue);
  }

  /* Contact side */
  .contact-glow {
    position: absolute; left: 0; top: 0; width: 470px; height: 360px;
    background: radial-gradient(ellipse at 50% 40%, rgba(120,40,60,0.35) 0%, rgba(40,30,80,0.25) 45%, rgba(20,60,60,0) 75%);
  }
  .contact-name {
    position: absolute; left: 70px; top: 336px;
    font-family: "Montserrat", sans-serif;
    font-weight: 700; font-size: 34px;
    color: var(--ink-white); letter-spacing: 1px;
  }
  .contact-title {
    font-family: "Questrial", sans-serif;
    font-weight: 400; font-size: 20px; letter-spacing: 1px;
    margin-left: 14px;
  }
  .contact-lines {
    position: absolute; left: 70px; top: 398px;
    display: flex; gap: 28px;
    font-size: 19px; color: var(--ink-white); letter-spacing: 0.5px;
  }
  .contact-line { display: flex; align-items: center; gap: 9px; }
  .contact-line svg { width: 18px; height: 18px; fill: var(--band-red); }
  .color-band {
    position: absolute; left: 0; right: 0; bottom: 0; height: 24px;
    display: flex; gap: 4px;
  }
  .color-band span { flex: 1; }
  .color-band .orange { background: var(--band-orange); }
  .color-band .red { background: var(--band-red); }
  .color-band .purple { background: var(--band-purple); }
  .color-band .cyan { background: var(--band-cyan); }
  .company-mark {
    position: absolute; right: 40px; top: 30px;
    width: 120px; height: 440px;
    display: flex; flex-direction: column; align-items: center; justify-content: space-between;
  }
  .company-mark__name {
    writing-mode: vertical-rl;
    transform: rotate(180deg);
    font-family: "Montserrat", sans-serif;
    font-weight: 700; font-size: 44px; letter-spacing: 5px;
    color: var(--ink-white);
  }
  .company-mark__dot {
    width: 64px; height: 64px; border-radius: 50%;
    background: var(--band-purple);
  }
</style>
</head>
<body>
  <section class="card card--product" aria-label="Product side">
    <div class="product-mark">
      <span class="product-mark__dot"></span>
      <span class="product-mark__name">Glimworld</span>
    </div>
    <p class="product-tagline">Culturally Immersive Language Learning Games</p>
    <p class="product-url">www.glimworld-play.com</p>
  </section>

  <section class="card card--contact" aria-label="Contact side">
    <div class="contact-glow" role="img" aria-label="Soft colour glow behind the contact details"></div>
    <h1 class="contact-name">PERRY DUNMORE<span class="contact-title">President</span></h1>
    <div class="contact-lines">
      <p class="contact-line">
        <svg viewBox="0 0 24 24" aria-hidden="true"><path d="M6.6 10.8a15.1 15.1 0 0 0 6.6 6.6l2.2-2.2a1 1 0 0 1 1-.25 11.4 11.4 0 0 0 3.6.57 1 1 0 0 1 1 1V20a1 1 0 0 1-1 1A17 17 0 0 1 3 4a1 1 0 0 1 1-1h3.5a1 1 0 0 1 1 1c0 1.25.2 2.45.57 3.6a1 1 0 0 1-.25 1z"/></svg>
        (555)-014-2286
      </p>
      <p class="contact-line">
        <svg viewBox="0 0 24 24" aria-hidden="true"><path d="M3 5h18a1 1 0 0 1 1 1v12a1 1 0 0 1-1 1H3a1 1 0 0 1-1-1V6a1 1 0 0 1 1-1zm1 2.3V17h16V7.3l-8 5.2z M4.8 7 12 11.6 19.2 7z"/></svg>
        pdunmore@quillpost-mail.net
      </p>
    </div>
    <div class="company-mark">
      <span class="company-mark__name">BRIGHTLOOM</span>
      <span class="company-mark__dot"></span>
    </div>
    <div class="color-band">
      <span class="orange"></span><span class="red"></span><span class="purple"></span><span class="cyan"></span>
    </div>
  </section>
</body>
</html>
```